Banner Ad Design Project

We need a 728x90 and a 300x250
1st option
"I have a lead for you. Click here to close the deal."
In large bold letters.
Under this in smaller letters,
"Lornavel. For serious business networkers"
2nd option
"Put that coffee down!"
"Coffee's for closers only."
Close more deals. LORNAVEL LOGO
(this is a quote from Harrowmere Tide. It is a famous sales movie)
The other option is
"First you get the money" "Then you get the power" in bold letters.
"Lornavel. For serious business networkers" in smaller letters at the bottom.
-Must have our colors
-Must have our logo (Small at the bottom right)
-Watch the video at lornavel () com
Please be creative. If the banner can have multiple images that would be great as well.
This needs to be a serious looking ad that is bold and clean.
Updates
Please be sure to use the phrase, "Put that coffee down! Coffee's for closers only" with the logo and at the bottom the words, Lornavel, for serious business networkers. in one of the designs. This will be our first campaign. I am looking for a very simple design that is bold. Perhaps just a coffee cup with the words and no other graphics.
Target Market(s)
Sales professionals
Industry/Entity Type
Business
Look and feel

```html
<!DOCTYPE html>
<html lang="en">
<head>
<meta charset="utf-8">
<title>Lornavel — Coffee's for closers only</title>
<link rel="stylesheet" href="https://fonts.googleapis.com/css2?family=Arimo:wght@400;700&display=swap">
<style>
  :root {
    --ink-white: #ffffff;
    --ink-dark: #1d1a16;
    --brand-orange: #e88a1a;
    --brand-blue: #2a8ec9;
    --tan-deep: #6b4a26;
    --tan-mid: #a8845a;
    --tan-light: #d9c3a0;
    --cream: #f3ead9;
    --paper: #ffffff;
  }
  * { margin: 0; padding: 0; box-sizing: border-box; }
  html, body { width: 1200px; height: 148px; overflow: hidden; background: var(--paper); }
  .banner {
    position: relative;
    width: 1200px;
    height: 148px;
    overflow: hidden;
    font-family: "Arimo", Arial, sans-serif;
    background: linear-gradient(90deg, var(--tan-mid) 0%, var(--tan-light) 60%, var(--cream) 74%, var(--paper) 86%);
  }
  .photo-handshake {
    position: absolute; left: 0; top: 0; width: 580px; height: 148px;
    background:
      radial-gradient(ellipse 260px 120px at 120px 110px, rgba(60,38,18,0.55), transparent 70%),
      linear-gradient(90deg, var(--tan-deep) 0%, var(--tan-mid) 45%, rgba(217,195,160,0.6) 80%, transparent 100%);
  }
  .photo-coffee {
    position: absolute; left: 560px; top: 0; width: 380px; height: 148px;
    background:
      radial-gradient(ellipse 150px 110px at 185px 78px, #8a6a44 0%, #b8976c 45%, rgba(232,218,194,0.9) 75%, transparent 100%);
  }
  .fade-right {
    position: absolute; left: 880px; top: 0; width: 320px; height: 148px;
    background: linear-gradient(90deg, rgba(255,255,255,0) 0%, var(--paper) 22%);
  }
  .headline { position: absolute; left: 30px; top: 8px; color: var(--ink-white); }
  .headline .kicker { font-size: 23px; font-weight: 400; line-height: 1.2; padding-left: 34px; }
  .headline .punch { font-size: 37px; font-weight: 700; line-height: 1.1; margin-top: 6px; letter-spacing: -0.3px; }
  .callout {
    position: absolute; left: 680px; top: 62px; width: 130px;
    color: var(--ink-white); font-size: 21px; font-weight: 700; line-height: 1.15; text-align: center;
  }
  .video-link { position: absolute; left: 880px; top: 14px; display: flex; align-items: center; gap: 14px; }
  .video-link .label { font-size: 17px; color: var(--ink-dark); }
  .brand { position: absolute; left: 980px; top: 82px; display: flex; align-items: center; gap: 12px; }
  .brand .mark { width: 40px; height: 40px; border-radius: 50%; background: var(--brand-orange); }
  .brand .name { font-size: 32px; font-weight: 700; color: var(--brand-blue); }
</style>
</head>
<body>
<div class="banner">
  <div class="photo-handshake" role="img" aria-label="Close-up photo of two business people shaking hands"></div>
  <div class="photo-coffee" role="img" aria-label="Photo of a hand holding a cup of coffee with milk"></div>
  <div class="fade-right"></div>

  <div class="headline">
    <p class="kicker">Put that coffee down!</p>
    <p class="punch">Coffee's for closers only.</p>
  </div>

  <p class="callout">Close more deals</p>

  <div class="video-link">
    <svg width="32" height="32" viewBox="0 0 32 32" aria-hidden="true">
      <circle cx="16" cy="16" r="15" fill="#1d1a16"/>
      <path d="M12 9 L23 16 L12 23 Z" fill="#ffffff"/>
    </svg>
    <span class="label">Watch the video at lornavel.com</span>
  </div>

  <div class="brand">
    <span class="mark"></span>
    <span class="name">Lornavel</span>
  </div>
</div>
</body>
</html>
```